Gobal construction supply company needs new business card design

I need a business card design for my global supply company using an existing logo. i will be looking to print these on rounded corner cards with the black background version of my logo on the back. on the front white background, my logo again and my simple details.

```html
<!DOCTYPE html>
<html lang="en">
<head>
<meta charset="utf-8">
<title>Meridian Build Supply – Business Card</title>
<link rel="stylesheet" href="https://fonts.googleapis.com/css2?family=Open+Sans:wght@400;600&display=swap">
<style>
  :root {
    --backdrop: #8e8c8a;
    --card-white: #f2f2f2;
    --card-black: #1b1b1b;
    --brand-red: #d80000;
    --ink-black: #111111;
    --ink-white: #ffffff;
  }
  html, body {
    margin: 0;
    padding: 0;
    overflow: hidden;
  }
  body {
    width: 1200px;
    height: 960px;
    background: var(--backdrop);
    font-family: "Open Sans", Arial, sans-serif;
    position: relative;
  }
  .card {
    position: absolute;
    width: 600px;
    height: 342px;
    border-radius: 18px;
  }
  .card-front {
    left: 82px;
    top: 103px;
    background: var(--card-white);
  }
  .card-back {
    left: 439px;
    top: 488px;
    background: var(--card-black);
  }
  .brand {
    position: absolute;
    text-align: center;
  }
  .brand-dot {
    display: block;
    margin: 0 auto;
    border-radius: 50%;
    background: var(--brand-red);
  }
  .brand-name {
    display: block;
    font-weight: 600;
    letter-spacing: 0.5px;
    text-transform: uppercase;
    white-space: nowrap;
  }
  .card-front .brand {
    left: 60px;
    width: 210px;
    top: 128px;
  }
  .card-front .brand-dot {
    width: 18px;
    height: 18px;
    margin-bottom: 12px;
  }
  .card-front .brand-name {
    color: var(--ink-black);
    font-size: 17px;
    line-height: 24px;
  }
  .card-back .brand {
    left: 150px;
    width: 300px;
    top: 106px;
  }
  .card-back .brand-dot {
    width: 24px;
    height: 24px;
    margin-bottom: 16px;
  }
  .card-back .brand-name {
    color: var(--ink-white);
    font-size: 22px;
    line-height: 30px;
  }
  .details-panel {
    position: absolute;
    left: 292px;
    top: 63px;
    width: 258px;
    height: 226px;
    border-radius: 16px;
    background: var(--brand-red);
    color: var(--ink-white);
    box-sizing: border-box;
    padding: 28px 0 0 31px;
  }
  .person-name {
    margin: 0;
    font-size: 20px;
    font-weight: 400;
    line-height: 24px;
  }
  .person-title {
    margin: 0 0 16px;
    font-size: 14px;
    line-height: 18px;
  }
  .contact-list {
    list-style: none;
    margin: 0 0 12px;
    padding: 0;
    font-size: 13px;
    line-height: 19px;
  }
  .contact-list li {
    display: flex;
    align-items: center;
  }
  .contact-icon {
    width: 12px;
    height: 12px;
    margin-right: 9px;
    fill: var(--ink-white);
    flex: none;
  }
  .address {
    margin: 0;
    font-size: 13px;
    line-height: 19px;
    font-style: normal;
  }
</style>
</head>
<body>
  <section class="card card-front" aria-label="Business card front">
    <div class="brand">
      <span class="brand-dot"></span>
      <span class="brand-name">Meridian Build</span>
      <span class="brand-name">Supply</span>
    </div>
    <div class="details-panel">
      <h1 class="person-name">DANIEL REEVE</h1>
      <p class="person-title">CEO/FOUNDER</p>
      <ul class="contact-list">
        <li>
          <svg class="contact-icon" viewBox="0 0 24 24" aria-hidden="true"><path d="M6.6 10.8c1.4 2.8 3.8 5.1 6.6 6.6l2.2-2.2c.3-.3.7-.4 1-.2 1.1.4 2.3.6 3.6.6.6 0 1 .4 1 1V20c0 .6-.4 1-1 1C10.6 21 3 13.4 3 4c0-.6.4-1 1-1h3.5c.6 0 1 .4 1 1 0 1.3.2 2.5.6 3.6.1.3 0 .7-.2 1z"/></svg>
          555 210 4836
        </li>
        <li>
          <svg class="contact-icon" viewBox="0 0 24 24" aria-hidden="true"><path d="M2 5h20v14H2z M3.5 6.5 12 13l8.5-6.5" fill="none" stroke="#fff" stroke-width="2"/><path d="M2 5h20L12 12.5z"/></svg>
          daniel@meridianbuild.com
        </li>
        <li>
          <svg class="contact-icon" viewBox="0 0 24 24" aria-hidden="true"><circle cx="12" cy="12" r="10"/><path d="M7 6c2 1 2 3 4 3s1 3-1 3-2 3 0 5M15 4c-1 2 1 3 2 3s2 2 1 4" fill="none" stroke="#d80000" stroke-width="1.8"/></svg>
          www.meridianbuild.com
        </li>
      </ul>
      <address class="address">1420 Harbor Street<br>Portland, Oregon 97205</address>
    </div>
  </section>

  <section class="card card-back" aria-label="Business card back">
    <div class="brand">
      <span class="brand-dot"></span>
      <span class="brand-name">Meridian Build Supply</span>
    </div>
  </section>
</body>
</html>
```